Business Card Design (NEW FILES)

ATTENTION: New vector files are available. Please update your design to reflect/use the new (better resolution) logo images.

Seeking a unique and professional business card design for a commercial drone photography/videography business. The layout should feature
the logo (attached) and include the following information:
Owen Tarrick
614-502-7738
www.skylarkreelworks.example
NRD Certified Remote Pilot

Owen Tarrick

```html
<!DOCTYPE html>
<html lang="en">
<head>
<meta charset="utf-8">
<title>Skylark Reelworks – Business Card</title>
<link href="https://fonts.googleapis.com/css2?family=Open+Sans:wght@400;600;700&display=swap" rel="stylesheet">
<style>
  :root {
    --stage: #222222;
    --navy: #1b1c4d;
    --orange: #ec8b55;
    --orange-deep: #e07a43;
    --orange-light: #f4a466;
    --white: #ffffff;
  }
  * { margin: 0; padding: 0; box-sizing: border-box; }
  html, body {
    width: 1200px; height: 780px; overflow: hidden;
    background: var(--stage);
    font-family: "Open Sans", Arial, sans-serif;
  }
  .stage { position: relative; width: 1200px; height: 780px; }

  /* Front of card (portrait) */
  .card-front {
    position: absolute; left: 130px; top: 110px;
    width: 340px; height: 560px;
    background: var(--navy);
    box-shadow: 0 18px 40px rgba(0,0,0,.55);
    overflow: hidden;
  }
  .card-front__header {
    height: 150px; background: var(--white);
    display: flex; align-items: center; justify-content: center; gap: 10px;
  }
  .brand-mark {
    flex: none;
    width: 14px; height: 14px; border-radius: 50%; background: var(--orange);
  }
  .brand-name {
    font-weight: 600; font-size: 24px; color: var(--navy); letter-spacing: .5px;
    white-space: nowrap;
  }
  .card-front__tab {
    position: absolute; right: 0; top: 336px;
    width: 12px; height: 40px; background: var(--orange);
  }
  .card-front__details {
    position: absolute; right: 30px; bottom: 34px; text-align: right;
    color: var(--white);
  }
  .person-name { font-size: 30px; font-weight: 700; line-height: 1.1; }
  .person-name__first { color: var(--orange); }
  .person-role { font-size: 15px; margin-bottom: 14px; }
  .credential { font-size: 14px; line-height: 1.5; }
  .contact {
    display: flex; align-items: center; justify-content: flex-end; gap: 8px;
    font-size: 14px; line-height: 1.6;
  }
  .contact:first-of-type { margin-top: 14px; }
  .contact svg { width: 14px; height: 14px; }

  /* Back of card (landscape) */
  .card-back {
    position: absolute; left: 540px; top: 220px;
    width: 560px; height: 340px;
    background: var(--orange);
    box-shadow: 0 18px 40px rgba(0,0,0,.55);
    overflow: hidden;
  }
  .card-back__brand {
    position: absolute; left: 30px; top: 130px;
    display: flex; align-items: center; gap: 8px;
  }
  .card-back__brand .brand-mark { background: var(--navy); width: 12px; height: 12px; }
  .card-back__brand .brand-name { font-size: 20px; }
  .card-back__illustration {
    position: absolute; left: 300px; top: 40px;
    width: 240px; height: 220px; border-radius: 50%;
    background: radial-gradient(ellipse at center, var(--orange-light) 0%, var(--orange) 70%);
    box-shadow: inset 2px 2px 6px rgba(0,0,0,.12), inset -2px -2px 6px rgba(255,255,255,.15);
  }
</style>
</head>
<body>
<main class="stage">
  <section class="card-front">
    <header class="card-front__header">
      <span class="brand-mark"></span>
      <span class="brand-name">Skylark Reelworks</span>
    </header>
    <span class="card-front__tab"></span>
    <div class="card-front__details">
      <p class="person-name"><span class="person-name__first">Owen</span> Tarrick</p>
      <p class="person-role">Owner</p>
      <p class="credential">NRD Certified Remote Pilot</p>
      <p class="credential">Fully Insured</p>
      <p class="contact">614-502-7738
        <svg viewBox="0 0 16 16" aria-hidden="true"><path fill="#ec8b55" d="M4 1l2.5 3-1.5 1.5c.8 2 2.5 3.7 4.5 4.5L11 8.5 14 11l-1.5 3C7 14 2 9 2 3z"/></svg>
      </p>
      <p class="contact">www.skylarkreelworks.example
        <svg viewBox="0 0 16 16" aria-hidden="true"><circle cx="8" cy="8" r="7" fill="#ec8b55"/><path d="M1 8h14M8 1c-3 3-3 11 0 14M8 1c3 3 3 11 0 14" stroke="#1b1c4d" stroke-width="1" fill="none"/></svg>
      </p>
    </div>
  </section>

  <section class="card-back">
    <div class="card-back__brand">
      <span class="brand-mark"></span>
      <span class="brand-name">Skylark Reelworks</span>
    </div>
    <div class="card-back__illustration" role="img" aria-label="Embossed drone illustration with camera"></div>
  </section>
</main>
</body>
</html>
```